Willow Fen Racquet Club (Tennis Country Club)

Racquet and Tennis Country Club in Florida.
This web sight is needed for a Privet Tennis club located in Deerfield Beach city in Florida, USA.
We have 10 clay tennis courts and 2 hard tennis courts, small and cozy swimming pool and a clubhouse (see attached pictures) Attached pictures are for information only because we are under a reconstruction.
Updates

I haven't received any source files and web converted files neither!

Target Market(s)

Adult members, Kids members, Tennis players

Coding

Coded - Design and coding required

Number of Pages Required

3 page

Requirements
Must have
• Logo colors (see attached file)

```html
<!DOCTYPE html>
<html lang="en">
<head>
<meta charset="utf-8">
<title>Willow Fen Racquet Club</title>
<link href="https://fonts.googleapis.com/css2?family=Libre+Franklin:wght@300;400;500;600;700;900&display=swap" rel="stylesheet">
<style>
  :root {
    --green: #1d6238;
    --green-bright: #2a7a46;
    --ink: #333333;
    --muted: #555555;
    --rule: #c9c9c9;
    --white: #ffffff;
    --footer: #2b2b2b;
    --hero-a: #3a4652;
    --hero-b: #2b3540;
    --hero-c: #24374f;
  }
  * { margin: 0; padding: 0; box-sizing: border-box; }
  html, body { width: 1200px; height: 2748px; overflow: hidden; }
  body {
    font-family: "Libre Franklin", Arial, sans-serif;
    color: var(--ink);
    background: var(--white);
    position: relative;
  }
  .page { position: relative; width: 1200px; height: 2748px; }

  /* Header */
  .site-header { position: absolute; top: 0; left: 0; width: 1200px; height: 106px; background: var(--white); }
  .brand { position: absolute; left: 100px; top: 8px; width: 150px; text-align: center; }
  .brand-dot { display: block; width: 54px; height: 54px; border-radius: 50%; background: var(--green); margin: 0 auto 6px; }
  .brand-name { font-size: 24px; font-weight: 600; color: var(--ink); letter-spacing: -0.3px; white-space: nowrap; }
  .main-nav a { position: absolute; top: 47px; font-size: 15px; color: #222; text-decoration: none; white-space: nowrap; }
  .main-nav a.is-active { color: var(--green); }

  /* Hero */
  .hero { position: absolute; top: 106px; left: 0; width: 1200px; height: 550px; overflow: hidden;
    background: linear-gradient(180deg, #55606c 0%, var(--hero-a) 35%, var(--hero-c) 65%, var(--hero-b) 100%); }
  .hero-shade { position: absolute; inset: 0; background: rgba(0,0,0,0.28); }
  .hero-title { position: absolute; top: 158px; left: 0; width: 1200px; text-align: center; font-size: 86px; font-weight: 900; color: var(--white); letter-spacing: 1px; line-height: 1; }
  .hero-sub { position: absolute; top: 252px; left: 0; width: 1200px; text-align: center; font-size: 18px; font-weight: 300; color: var(--white); }
  .btn-start { position: absolute; top: 299px; left: 517px; width: 166px; height: 40px; background: var(--green-bright); color: var(--white); font-size: 18px; font-weight: 700; text-align: center; line-height: 40px; }
  .hero-arrow { position: absolute; top: 278px; }

  /* Welcome */
  .welcome { position: absolute; top: 656px; left: 0; width: 1200px; height: 507px; }
  .welcome-title { position: absolute; top: 76px; width: 1200px; text-align: center; font-size: 37px; font-weight: 300; color: var(--green); }
  .divider-line { position: absolute; top: 150px; height: 1px; background: var(--rule); }
  .divider-mark { position: absolute; top: 130px; left: 560px; width: 80px; text-align: center; }
  .divider-mark .dot { display: block; width: 28px; height: 28px; border-radius: 50%; background: var(--green); margin: 0 auto 3px; }
  .divider-mark .name { font-size: 11px; font-weight: 600; color: var(--ink); white-space: nowrap; }
  .welcome-copy { position: absolute; left: 150px; width: 900px; text-align: center; font-size: 16.5px; font-weight: 300; line-height: 28px; color: var(--muted); }

  /* Facilities */
  .facilities { position: absolute; top: 1163px; left: 0; width: 1200px; height: 523px; background: var(--green); overflow: hidden; }
  .section-title { position: absolute; width: 1200px; text-align: center; font-size: 37px; font-weight: 600; }
  .facilities .section-title { top: 67px; color: var(--white); }
  .facility { position: absolute; top: 165px; width: 260px; text-align: center; }
  .facility-photo { width: 202px; height: 202px; border-radius: 50%; border: 7px solid var(--white); margin: 0 auto; }
  .facility-label { margin-top: 30px; font-size: 15.5px; font-weight: 400; color: var(--white); text-transform: uppercase; }

  /* Testimonials */
  .testimonials { position: absolute; top: 1686px; left: 0; width: 1200px; height: 540px; }
  .testimonials .section-title { top: 68px; color: var(--ink); }
  .quote-mark { position: absolute; top: 130px; left: 98px; font-size: 80px; font-weight: 700; color: #cfcfcf; line-height: 1; }
  .quote-text { position: absolute; top: 152px; left: 155px; width: 890px; text-align: center; font-size: 17px; font-weight: 300; line-height: 25px; color: var(--muted); }
  .client { position: absolute; top: 272px; width: 92px; height: 92px; border-radius: 50%; background: radial-gradient(circle at 50% 40%, #9a9a9a, #4a4a4a); }
  .client-featured-ring { position: absolute; top: 243px; left: 525px; width: 150px; height: 150px; border-radius: 50%; border: 1px solid #e4e4e4; background: var(--white); }
  .client-featured { position: absolute; top: 259px; left: 541px; width: 118px; height: 118px; border-radius: 50%; background: radial-gradient(circle at 50% 40%, #3f5aa8, #1b2a5e); }
  .slider-arrow { position: absolute; top: 288px; }
  .client-rule { position: absolute; top: 412px; left: 125px; width: 950px; height: 2px; background: #d6d6d6; }
  .client-rule-active { position: absolute; top: 410px; left: 559px; width: 82px; height: 4px; background: var(--green); }
  .client-name { position: absolute; top: 434px; width: 1200px; text-align: center; font-size: 18px; font-weight: 700; color: var(--green); }

  /* Contact */
  .contact { position: absolute; top: 2226px; left: 0; width: 1200px; height: 454px; overflow: hidden;
    background: linear-gradient(180deg, #5a6470 0%, #6f7268 45%, #6d6a55 70%, #4f6f78 100%); }
  .contact-shade { position: absolute; inset: 0; background: rgba(20,20,20,0.5); }
  .contact .section-title { top: 72px; color: var(--white); }
  .contact-sub { position: absolute; top: 126px; width: 1200px; text-align: center; font-size: 17px; font-weight: 300; color: var(--white); }
  .contact-item { position: absolute; top: 200px; height: 46px; display: flex; align-items: center; gap: 10px; font-size: 35px; font-weight: 300; color: var(--white); white-space: nowrap; }
  .btn-touch { position: absolute; top: 289px; left: 515px; width: 172px; height: 48px; border: 2px solid var(--white); color: var(--white); font-size: 16px; font-weight: 500; text-align: center; line-height: 44px; }

  /* Footer */
  .site-footer { position: absolute; top: 2680px; left: 0; width: 1200px; height: 68px; background: var(--footer); }
  .footer-note { position: absolute; top: 26px; width: 1200px; text-align: center; font-size: 12px; color: #d8d8d8; }
</style>
</head>
<body>
<div class="page">

  <header class="site-header">
    <div class="brand">
      <span class="brand-dot"></span>
      <span class="brand-name">Willow Fen</span>
    </div>
    <nav class="main-nav">
      <a class="is-active" style="left:471px">Home</a>
      <a style="left:559px">About Us</a>
      <a style="left:670px">Our Services</a>
      <a style="left:808px">Testimonials</a>
      <a style="left:945px">Blog</a>
      <a style="left:1024px">Contact Us</a>
    </nav>
  </header>

  <section class="hero" role="img" aria-label="Photo of the club's tennis courts under floodlights with a rainbow in the evening sky">
    <div class="hero-shade"></div>
    <h1 class="hero-title">WILLOW FEN</h1>
    <p class="hero-sub">Private Tennis club located in Deerfield Beach city in Florida, USA.</p>
    <div class="btn-start">START NOW !</div>
    <svg class="hero-arrow" style="left:36px" width="14" height="36" viewBox="0 0 14 36"><polyline points="13,1 1,18 13,35" fill="none" stroke="#ffffff" stroke-opacity="0.7" stroke-width="1.5"/></svg>
    <svg class="hero-arrow" style="left:1140px" width="14" height="36" viewBox="0 0 14 36"><polyline points="1,1 13,18 1,35" fill="none" stroke="#ffffff" stroke-opacity="0.7" stroke-width="1.5"/></svg>
  </section>

  <section class="welcome">
    <h2 class="welcome-title">WELCOME TO WILLOW FEN</h2>
    <div class="divider-line" style="left:256px; width:294px"></div>
    <div class="divider-line" style="left:650px; width:295px"></div>
    <div class="divider-mark"><span class="dot"></span><span class="name">Willow Fen</span></div>
    <p class="welcome-copy" style="top:208px">Sed ut perspiciatis unde omnis iste natus error sit voluptatem accusantium doloremque laudantium, totam rem aperiam, eaque ipsa quae ab illo inventore veritatis et quasi architecto beatae vitae dicta sunt explicabo. Nemo enim ipsam voluptatem quia voluptas sit aspernatur aut odit aut fugit, sed quia consequuntur magni dolores eos qui ratione voluptatem sequi nesciunt</p>
    <p class="welcome-copy" style="top:342px">Quis autem vel eum iure reprehenderit qui in ea voluptate velit esse quam nihil molestiae consequatur, vel illum qui dolorem eum fugiat quo voluptas nulla pariatur.</p>
  </section>

  <section class="facilities">
    <h2 class="section-title">WHAT WE HAVE</h2>
    <div class="facility" style="left:71px">
      <div class="facility-photo" role="img" aria-label="Rendering of the covered clay tennis courts" style="background:linear-gradient(160deg,#8a7a6a,#5d5a58 60%,#3e4a44)"></div>
      <div class="facility-label">10 clay tennis courts</div>
    </div>
    <div class="facility" style="left:341px">
      <div class="facility-photo" role="img" aria-label="Rendering of the hard tennis courts pavilion" style="background:linear-gradient(160deg,#e8e8e8,#a9a9a9 55%,#5f8e86)"></div>
      <div class="facility-label">2 hard tennis courts</div>
    </div>
    <div class="facility" style="left:605px">
      <div class="facility-photo" role="img" aria-label="Photo of the small swimming pool" style="background:linear-gradient(170deg,#4d6a3e,#2f86c8 35%,#1d5fa3)"></div>
      <div class="facility-label">Small and cozy swimming pool</div>
    </div>
    <div class="facility" style="left:868px">
      <div class="facility-photo" role="img" aria-label="Rendering of the clubhouse" style="background:linear-gradient(170deg,#f2f2f2,#d9d9d9 55%,#8a8a8a)"></div>
      <div class="facility-label">Clubhouse</div>
    </div>
  </section>

  <section class="testimonials">
    <h2 class="section-title">WHAT OUR CLIENTS SAY?</h2>
    <div class="quote-mark">&ldquo;</div>
    <p class="quote-text">At vero eos et accusamus et iusto odio dignissimos ducimus qui blanditiis praesentium voluptatum deleniti atque corrupti quos dolores et quas molestias excepturi sint occaecati cupiditate non provident</p>
    <svg class="slider-arrow" style="left:104px" width="22" height="56" viewBox="0 0 22 56"><polyline points="21,1 1,28 21,55" fill="none" stroke="#cccccc" stroke-width="1.5"/></svg>
    <div class="client" style="left:168px" role="img" aria-label="Portrait of a club member"></div>
    <div class="client" style="left:306px" role="img" aria-label="Photo of a club member playing tennis"></div>
    <div class="client-featured-ring"></div>
    <div class="client-featured" role="img" aria-label="Photo of the featured member John Doe playing tennis"></div>
    <div class="client" style="left:802px" role="img" aria-label="Photo of a club member serving"></div>
    <div class="client" style="left:921px" role="img" aria-label="Photo of a club member on court"></div>
    <svg class="slider-arrow" style="left:1078px" width="22" height="56" viewBox="0 0 22 56"><polyline points="1,1 21,28 1,55" fill="none" stroke="#cccccc" stroke-width="1.5"/></svg>
    <div class="client-rule"></div>
    <div class="client-rule-active"></div>
    <div class="client-name">JOHN DOE</div>
  </section>

  <section class="contact" role="img" aria-label="Blurred aerial photo of the Florida coastline and city">
    <div class="contact-shade"></div>
    <h2 class="section-title">CONTACT WILLOW FEN</h2>
    <p class="contact-sub">Contact us the following general enquiries</p>
    <div class="contact-item" style="left:196px">
      <svg width="30" height="30" viewBox="0 0 24 24"><path fill="#ffffff" d="M6.6 10.8c1.4 2.8 3.8 5.1 6.6 6.6l2.2-2.2c.3-.3.7-.4 1-.2 1.1.4 2.3.6 3.6.6.6 0 1 .4 1 1V20c0 .6-.4 1-1 1C10.6 21 3 13.4 3 4c0-.6.4-1 1-1h3.5c.6 0 1 .4 1 1 0 1.3.2 2.5.6 3.6.1.3 0 .7-.2 1l-2.3 2.2z"/></svg>
      <span>1- 800 - 55501234</span>
    </div>
    <div class="contact-item" style="left:617px">
      <svg width="34" height="28" viewBox="0 0 34 28"><rect x="0" y="2" width="34" height="24" rx="2" fill="#ffffff"/><polyline points="1,4 17,16 33,4" fill="none" stroke="#5a5d5a" stroke-width="2.4"/></svg>
      <span>info@willowfen.com</span>
    </div>
    <div class="btn-touch">GET IN TOUCH</div>
  </section>

  <footer class="site-footer">
    <p class="footer-note">&copy; 2018 Willow Fen.&nbsp; All right reserved . Term of Use</p>
  </footer>

</div>
</body>
</html>
```